Spring Detox sale graphics for social media

You MUST read the Brief in the WORD document and follow the instructions there. I want to create 10 social media graphics (new Instagram size 4:5 (1080 x 1350 pixels) focusing on our Mother’s Day Spring Detox Sale graphics, using any of the pics attached. Use the attached pics, NO RANDOM STOCK PHOTOGRAPHY. For the color scheme of the graphics, they should all be complementary to the product colors or feel like Spring time.

Target Market(s)

primarily women

Requirements
Must have
• the photos and text attached

```html
<!DOCTYPE html>
<html lang="en">
<head>
<meta charset="utf-8">
<title>Mother's Day Spring Detox Sale – Social Set</title>
<link href="https://fonts.googleapis.com/css2?family=Oswald:wght@500;600;700&family=Lexend:wght@600;700&display=swap" rel="stylesheet">
<style>
  :root{
    --stage:#000000;
    --white:#ffffff;
    --blush:#fff7f8;
    --mint:#e9faef;
    --ice:#eef9fc;
    --forest:#2a5a30;
    --teal-green:#1d6a4f;
    --leaf:#14891e;
    --pink:#de4f9c;
    --magenta:#cf1b7c;
    --purple:#8a3a9a;
    --plum:#5b2d4f;
    --mauve:#4a3a45;
    --red:#f2002a;
    --flame:#f01c0a;
    --maroon:#560d0d;
    --navy:#1c24a0;
    --soft-pink:#f5a3c2;
    --bottle:#e4e6ea;
    --bottle-edge:#c9ccd4;
  }
  *{box-sizing:border-box;margin:0;padding:0}
  html,body{width:1200px;height:2652px;overflow:hidden;background:var(--stage)}
  .canvas{position:relative;width:1200px;height:2652px;background:var(--stage)}
  .post{position:absolute;width:345px;height:430px;overflow:hidden;background:var(--white)}
  .col-a{left:248px}.col-b{left:606px}
  .row-1{top:215px}.row-2{top:662px}.row-3{top:1109px}.row-4{top:1557px}.row-5{top:2005px}
  .t{position:absolute;font-family:'Oswald',sans-serif;font-weight:600;line-height:.9;white-space:nowrap;letter-spacing:-.5px}
  .round{font-family:'Lexend',sans-serif;font-weight:700;letter-spacing:0}
  .deal{position:absolute;display:flex;align-items:flex-start;font-family:'Oswald',sans-serif;font-weight:600;line-height:.85}
  .deal .num{letter-spacing:-2px}
  .deal .side{display:flex;flex-direction:column;margin-left:4px}
  .deal .pct{font-weight:500}
  .center{left:0;right:0;text-align:center}
  .bottles{position:absolute;border-radius:6px;background:linear-gradient(180deg,var(--bottle),#f7f7f9 60%,var(--bottle-edge))}
  .photo{position:absolute;inset:0;background:linear-gradient(160deg,#7a4a32 0%,#5a3524 45%,#9a8f88 75%,#d9d6d2 100%)}
  .badge{position:absolute;width:92px;height:92px;border-radius:50%;background:var(--soft-pink);color:var(--white)}
</style>
</head>
<body>
<main class="canvas">

  <!-- 1 -->
  <section class="post col-a row-1" style="background:var(--blush)">
    <div class="t" style="left:22px;top:44px;font-size:44px;color:var(--forest)">MOTHER’S DAY</div>
    <div class="t" style="left:20px;top:94px;font-size:96px;color:var(--pink)">SPRING</div>
    <div class="t" style="left:20px;top:186px;font-size:70px;color:var(--pink)">Detox Sale</div>
    <div class="deal" style="left:20px;top:276px;color:var(--forest)">
      <span class="num" style="font-size:96px">25</span>
      <span class="side"><span class="pct" style="font-size:48px">%</span><span style="font-size:32px">OFF</span></span>
    </div>
    <div class="t round" style="left:170px;top:292px;font-size:16px;color:var(--forest)">Everything!</div>
    <div class="bottles" role="img" aria-label="Four supplement bottles" style="left:170px;top:330px;width:155px;height:92px"></div>
  </section>

  <!-- 2 -->
  <section class="post col-b row-1" style="background:var(--mint)">
    <div class="bottles" role="img" aria-label="Four supplement bottles in a row" style="left:44px;top:10px;width:260px;height:118px"></div>
    <div class="deal" style="left:46px;top:134px;color:var(--teal-green)">
      <span class="num" style="font-size:80px">25</span>
      <span class="side"><span class="pct" style="font-size:40px">%</span><span style="font-size:30px">OFF</span></span>
    </div>
    <div class="t" style="left:46px;top:216px;font-size:48px;color:var(--teal-green)">Mother’s Day</div>
    <div class="t" style="left:46px;top:266px;font-size:84px;color:var(--purple)">Spring</div>
    <div class="t" style="left:46px;top:356px;font-size:54px;color:var(--purple)">DETOX SALE</div>
  </section>

  <!-- 3 -->
  <section class="post col-a row-2" style="background:linear-gradient(160deg,var(--white) 50%,var(--ice) 50%)">
    <div class="deal" style="left:74px;top:48px;color:var(--plum)">
      <span class="num" style="font-size:120px">25</span>
      <span class="side"><span class="pct" style="font-size:62px">%</span><span style="font-size:46px">OFF</span></span>
    </div>
    <div class="t round center" style="top:162px;font-size:28px;font-weight:600;color:var(--plum)">All Supplements</div>
    <div class="t center" style="top:200px;font-size:98px;color:var(--pink)">SPRING</div>
    <div class="t center" style="top:296px;font-size:60px;color:var(--pink)">DETOX SALE</div>
  </section>

  <!-- 4 -->
  <section class="post col-b row-2">
    <div class="deal" style="left:12px;top:44px;color:var(--forest)">
      <span class="num" style="font-size:96px">25</span>
      <span class="side"><span class="pct" style="font-size:46px">%</span><span style="font-size:36px">OFF</span></span>
    </div>
    <div class="bottles" role="img" aria-label="Four supplement bottles" style="left:176px;top:36px;width:160px;height:94px"></div>
    <div class="t" style="right:10px;top:148px;font-size:50px;color:var(--pink)">SPRING DETOX</div>
    <div class="bottles" role="img" aria-label="Small supplement bottles" style="left:2px;top:216px;width:122px;height:56px"></div>
    <div class="t" style="right:10px;top:204px;font-size:106px;color:var(--pink)">SALE</div>
    <div class="t round" style="left:26px;top:312px;font-size:32px;letter-spacing:2px;color:var(--forest);line-height:1.25">Spring&nbsp; Reset<br>Summer&nbsp; Ready</div>
  </section>

  <!-- 5 -->
  <section class="post col-a row-3">
    <div class="deal" style="left:28px;top:44px;color:var(--mauve)">
      <span class="num" style="font-size:104px">25</span>
      <span class="side"><span class="pct" style="font-size:52px">%</span><span style="font-size:38px">OFF</span></span>
    </div>
    <div class="t round" style="left:198px;top:78px;font-size:18px;color:var(--mauve)">Everything!</div>
    <div class="t" style="left:32px;top:150px;font-size:50px;color:var(--mauve)">MOTHER’S DAY</div>
    <div class="t" style="left:30px;top:210px;font-size:94px;color:var(--red)">SPRING</div>
    <div class="t" style="left:30px;top:308px;font-size:62px;color:var(--red)">DETOX SALE</div>
  </section>

  <!-- 6 -->
  <section class="post col-b row-3">
    <div class="deal" style="left:84px;top:28px;color:var(--flame);font-weight:700">
      <span class="num" style="font-size:90px">25</span>
      <span class="side"><span class="pct" style="font-size:48px">%</span><span style="font-size:34px">OFF</span></span>
    </div>
    <div class="t center" style="top:122px;font-size:46px;color:var(--maroon)">MOTHER’S DAY</div>
    <div class="t center" style="top:168px;font-size:122px;font-weight:700;color:var(--maroon)">SALE</div>
    <div class="t center" style="top:286px;font-size:56px;color:var(--flame);line-height:1.02">Feel Amazing<br>Again!</div>
  </section>

  <!-- 7 -->
  <section class="post col-a row-4">
    <div class="deal" style="left:88px;top:32px;color:var(--leaf)">
      <span class="num" style="font-size:100px">25</span>
      <span class="side"><span class="pct" style="font-size:50px">%</span><span style="font-size:36px">OFF</span></span>
    </div>
    <div class="t center" style="top:136px;font-size:68px;color:var(--navy);line-height:.93">MOTHER’S<br>DAY SALE</div>
    <div class="t center" style="top:274px;font-size:62px;color:var(--leaf);line-height:.92">REFRESH<br>YOUR BODY</div>
  </section>

  <!-- 8 -->
  <section class="post col-b row-4">
    <div class="photo" role="img" aria-label="Smiling woman in a white sweater in a kitchen, with supplement bottles in front"></div>
    <div class="t center" style="top:12px;padding-left:12px;font-size:46px;color:var(--white)">SPRING DETOX</div>
    <div class="t" style="left:10px;top:118px;font-size:64px;color:var(--white)">SALE</div>
    <div class="badge" style="left:242px;top:78px">
      <div class="deal" style="left:12px;top:24px;color:var(--white)">
        <span class="num" style="font-size:44px">25</span>
        <span class="side"><span class="pct" style="font-size:22px">%</span><span style="font-size:16px">OFF</span></span>
      </div>
    </div>
    <div class="t" style="left:10px;top:204px;font-size:30px;font-weight:500;color:var(--white);line-height:1.2">Spring<br>Cleanse</div>
    <div class="t" style="left:10px;top:300px;font-size:22px;font-weight:500;color:var(--white);line-height:1.15">Summer<br>Glow</div>
  </section>

  <!-- 9 -->
  <section class="post col-a row-5">
    <div class="deal" style="left:94px;top:30px;color:var(--navy)">
      <span class="num" style="font-size:96px">25</span>
      <span class="side"><span class="pct" style="font-size:48px">%</span><span style="font-size:34px">OFF</span></span>
    </div>
    <div class="t center" style="top:130px;font-size:48px;color:var(--magenta)">MOTHER’S DAY</div>
    <div class="t center" style="top:180px;font-size:126px;font-weight:700;color:var(--navy)">SALE</div>
    <div class="t round center" style="top:328px;font-size:27px;font-weight:600;color:var(--magenta);line-height:1.35">Detox This Spring.<br>Shine This Summer</div>
  </section>

  <!-- 10 -->
  <section class="post col-b row-5">
    <div class="deal" style="left:34px;top:48px;color:var(--leaf)">
      <span class="num" style="font-size:84px">25</span>
      <span class="side"><span class="pct" style="font-size:42px">%</span><span style="font-size:32px">OFF</span></span>
    </div>
    <div class="bottles" role="img" aria-label="Four supplement bottles" style="left:172px;top:24px;width:170px;height:96px"></div>
    <div class="t" style="left:34px;top:140px;font-size:50px;color:var(--navy)">MOTHER’S DAY</div>
    <div class="t" style="left:32px;top:194px;font-size:86px;font-weight:700;color:var(--navy)">SALE</div>
    <div class="t" style="left:34px;top:282px;font-size:54px;color:var(--magenta)">Spring Detox</div>
    <div class="t" style="left:34px;top:346px;font-size:36px;color:var(--magenta)">for a Summer Body</div>
  </section>

</main>
</body>
</html>
```